Velk Partners Building Business Cards

We need a business card that reflects our business as "Solar Experts" in San Diego. Browse our website www.velkpartners.example our License needs to be displayed as "CSLB# 3867140" our phone number is (619) 555-0187

Save thousands on your electric bills and increase the value of your home while helping to protect the environment. Our solar installation experts will help you design the system that's right for you, using only the highest quality equipment that will look great and give you ideal performance. Our goal is to make you energy independent, and get your electric bill to 0.

Paul Osterby
(619) 555-0187
paul@velkpartners.example

Target Market(s)

Home owners in san diego looking for solar

Industry/Entity Type

Solar Energy

Contact Information for Business Card

Paul Osterby
(619) 555-0187
paul@velkpartners.example

Font styles to use
Other font styles liked:
• Use our logo font

Requirements
Must have
• License needs to be displayed as "CSLB# 3867140" our phone number is (619) 555-0187
Nice to have
• Real images of rooftop home solar in san diego
Should not have
• our business address

```html
<!DOCTYPE html>
<html lang="en">
<head>
<meta charset="utf-8">
<title>Velk Partners Building — Business Cards</title>
<link rel="stylesheet" href="https://fonts.googleapis.com/css2?family=Open+Sans:wght@400;600;700&display=swap">
<style>
  :root {
    --backdrop: #4a423d;
    --card: #0d0d0d;
    --brand-blue: #2a4a98;
    --sun-gold: #f5b000;
    --name-orange: #f2a516;
    --text-light: #f2f2f2;
    --divider: #c9930f;
  }
  * { box-sizing: border-box; margin: 0; padding: 0; }
  html, body {
    width: 1200px;
    height: 900px;
    overflow: hidden;
    background: var(--backdrop);
    font-family: "Open Sans", Arial, sans-serif;
  }
  .canvas { position: relative; width: 1200px; height: 900px; }

  .card {
    position: absolute;
    background: var(--card);
    border-radius: 4px;
    box-shadow: 0 14px 30px rgba(0,0,0,0.45);
  }

  /* Logo side */
  .card-brand {
    left: 560px; top: 60px; width: 590px; height: 330px;
    display: flex; align-items: center; justify-content: center;
  }
  .brand-wordmark {
    color: var(--brand-blue);
    font-weight: 700;
    font-size: 44px;
    letter-spacing: -0.5px;
  }

  /* Contact side */
  .card-contact {
    left: 50px; top: 420px; width: 640px; height: 370px;
  }
  .brand-mark {
    position: absolute; left: 70px; top: 110px; width: 210px;
    display: flex; flex-direction: column; align-items: center; gap: 16px;
  }
  .brand-mark .dot {
    width: 110px; height: 110px; border-radius: 50%;
    background: var(--sun-gold);
  }
  .brand-mark .label {
    color: var(--brand-blue);
    font-weight: 700;
    font-size: 19px;
    text-align: center;
    line-height: 1.2;
  }
  .divider {
    position: absolute; left: 315px; top: 95px;
    width: 1px; height: 180px;
    background: linear-gradient(to bottom, transparent, var(--divider) 25%, var(--divider) 75%, transparent);
  }
  .details {
    position: absolute; left: 345px; top: 118px;
    color: var(--text-light);
  }
  .person-name {
    color: var(--name-orange);
    font-weight: 700;
    font-size: 19px;
    margin-bottom: 26px;
  }
  .license { font-size: 16px; margin-bottom: 10px; }
  .license strong { font-weight: 700; }
  .contact-line {
    display: flex; align-items: center; gap: 10px;
    font-size: 16px; margin-bottom: 4px;
  }
  .contact-line svg { width: 12px; height: 12px; flex: none; }
</style>
</head>
<body>
<main class="canvas">

  <section class="card card-brand">
    <span class="brand-wordmark">Velk Partners Building</span>
  </section>

  <section class="card card-contact">
    <div class="brand-mark">
      <span class="dot"></span>
      <span class="label">Velk Partners Building</span>
    </div>

    <div class="divider"></div>

    <div class="details">
      <p class="person-name">Paul Osterby</p>
      <p class="license"><strong>License:</strong> CSLB# 3867140</p>
      <p class="contact-line">
        <svg viewBox="0 0 24 24" aria-hidden="true"><path fill="#f5b000" d="M6.6 10.8a15.1 15.1 0 0 0 6.6 6.6l2.2-2.2a1 1 0 0 1 1-.25 11.4 11.4 0 0 0 3.6.57 1 1 0 0 1 1 1V20a1 1 0 0 1-1 1A17 17 0 0 1 3 4a1 1 0 0 1 1-1h3.5a1 1 0 0 1 1 1c0 1.25.2 2.45.57 3.57a1 1 0 0 1-.25 1z"/></svg>
        (619) 555-0187
      </p>
      <p class="contact-line">
        <svg viewBox="0 0 24 24" aria-hidden="true"><rect x="2" y="5" width="20" height="14" rx="1" fill="#f5b000"/><path d="M2 6l10 7 10-7" fill="none" stroke="#0d0d0d" stroke-width="2"/></svg>
        paul@velkpartners.example
      </p>
    </div>
  </section>

</main>
</body>
</html>
```